Interval Timer App

Need to have design for the attached wireframe. Similar app can be found here: https://shop.lumaverse.net/store/apps/details?id=cc.quillfern.pulseclock

```html
<!DOCTYPE html>
<html lang="en">
<head>
<meta charset="utf-8">
<title>Interval Timer – Get ready</title>
<link href="https://fonts.googleapis.com/css2?family=Noto+Sans:wght@400;500;600&display=swap" rel="stylesheet">
<style>
  :root {
    --bg-top: #fdf45c;
    --bg-bottom: #f9d40c;
    --card: #ffffff;
    --ink: #23222b;
    --accent: #1a7fe0;
  }
  * { margin: 0; padding: 0; box-sizing: border-box; }
  html, body { width: 675px; height: 1200px; overflow: hidden; }
  body {
    position: relative;
    background: linear-gradient(180deg, var(--bg-top) 0%, var(--bg-bottom) 100%);
    font-family: "Noto Sans", Arial, sans-serif;
    color: var(--ink);
  }
  .back-button {
    position: absolute;
    left: 26px;
    top: 36px;
    width: 34px;
    height: 40px;
  }
  .countdown-card {
    position: absolute;
    left: 30px;
    top: 281px;
    width: 615px;
    height: 638px;
    background: var(--card);
    border-radius: 19px;
    box-shadow: 0 2px 6px rgba(0,0,0,0.06);
  }
  .card-title {
    position: absolute;
    top: 50px;
    width: 100%;
    text-align: center;
    font-size: 38px;
    font-weight: 500;
    letter-spacing: 0.3px;
  }
  .progress-ring {
    position: absolute;
    left: 0;
    top: 0;
  }
  .countdown-value {
    position: absolute;
    left: 0;
    top: 272px;
    width: 626px;
    text-align: center;
    font-size: 86px;
    font-weight: 600;
    line-height: 1;
    color: var(--accent);
  }
  .sets-count {
    position: absolute;
    top: 522px;
    width: 626px;
    text-align: center;
    font-size: 35px;
    font-weight: 400;
    color: var(--accent);
  }
  .sets-label {
    position: absolute;
    top: 580px;
    width: 626px;
    text-align: center;
    font-size: 26px;
    font-weight: 500;
  }
</style>
</head>
<body>
  <svg class="back-button" viewBox="0 0 34 40" aria-label="Back">
    <path d="M24 4 L8 20 L24 36" fill="none" stroke="var(--accent)" stroke-width="4.5" stroke-linecap="round" stroke-linejoin="round"/>
  </svg>

  <section class="countdown-card">
    <h1 class="card-title">Get ready!</h1>
    <svg class="progress-ring" width="615" height="638" viewBox="30 281 615 638" aria-hidden="true">
      <path d="M343 451 A157 157 0 1 1 186.3 598" fill="none" stroke="var(--ink)" stroke-width="4.5" stroke-linecap="round"/>
      <circle cx="186.3" cy="598" r="13" fill="var(--accent)"/>
    </svg>
    <div class="countdown-value">04</div>
    <div class="sets-count">3</div>
    <div class="sets-label">sets</div>
  </section>
</body>
</html>
```